Valdo Capital

We need a corporate style website design for a new company based in Shenzhen's Qianhai Special Economic Development Zone, China. We provide a range of financial services to large international investment companies. Typically these companies invest over 5 million RMB. The company is part of a group that consists of NorthKilns, ValdoTrusts and ValdoEquity. Our location and gateway into Qianhai Special Economic Zone is our core advantage. We would like to see designs that Do Not use purple and orange. The website design should be similar to other websites in this family but different enough to give it a unique style (See attached website links for reference). The final design should communicate financial safety and growth. This website will act partly as a business chamber with connections to the government so we would like it to be diplomatic in style.

www.northkilns.example
www.valdotrusts.example

*Nevegation Bar
Should including Homepage, Financial Product, Team, News.
Could refer to www.valdotrusts.example

*Contact Details

Miss Lan
Address:E 728, North Block, KMO Centre, East Sector, Shenzhen Bright Science Campus
Telephone: +86 0755 63920417
Cellphone: +86 13957280316

* Social Media
Should be grouped like:
1. Weibo QRcode+ Weibo
2. Facebook, Twitter, Linkedin.

Industry/Entity Type

Investment

```html
<!DOCTYPE html>
<html lang="en">
<head>
<meta charset="utf-8">
<title>Valdo Capital</title>
<link href="https://fonts.googleapis.com/css2?family=Open+Sans:wght@300;400;600&family=Raleway:wght@500;600&display=swap" rel="stylesheet">
<style>
  :root {
    --night-deep: #0d1a2e;
    --night-blue: #1f3a5c;
    --city-glow: #8a6a4a;
    --shade: rgba(8, 8, 12, 0.72);
    --white: #ffffff;
    --soft-white: #e6e9ee;
    --muted: #a9b0ba;
    --ink: #111418;
    --button-text: #1e2228;
    --accent: #2aa6d8;
  }
  * { margin: 0; padding: 0; box-sizing: border-box; }
  html, body { width: 1200px; height: 984px; overflow: hidden; background: var(--night-deep); }
  body { font-family: "Open Sans", Arial, sans-serif; color: var(--white); }
  .page { position: relative; width: 1200px; height: 984px; overflow: hidden; }

  .hero-backdrop { position: absolute; inset: 0; }
  .hero-shade { position: absolute; inset: 0; }

  .brand { position: absolute; left: 110px; top: 38px; display: flex; align-items: center; gap: 14px; }
  .brand-mark { width: 38px; height: 38px; border-radius: 50%; background: var(--accent); }
  .brand-name { font-size: 34px; font-weight: 400; letter-spacing: 1px; color: var(--white); }

  .lang { position: absolute; left: 917px; top: 22px; font-size: 13px; color: var(--muted); }
  .lang .current { color: var(--soft-white); text-decoration: underline; }
  .lang .caret { display: inline-block; margin-left: 8px; border: 4px solid transparent; border-top-color: var(--muted); vertical-align: -1px; }
  .social { position: absolute; left: 997px; top: 18px; display: flex; gap: 6px; }
  .social span { width: 28px; height: 28px; border-radius: 50%; background: #8d9299; box-shadow: inset 0 0 0 2px #6b7077; }

  .main-nav { position: absolute; right: 110px; top: 65px; display: flex; gap: 30px; font-size: 13px; }
  .main-nav a { color: var(--soft-white); text-decoration: none; opacity: .85; }
  .main-nav a.active { color: var(--white); opacity: 1; }

  .welcome { position: absolute; left: 114px; top: 232px; }
  .welcome .lead { font-size: 62px; font-weight: 300; color: var(--ink); letter-spacing: -2px; line-height: 70px; }
  .welcome h1 { font-size: 64px; font-weight: 600; line-height: 70px; letter-spacing: -1px; }
  .welcome p { margin-top: 10px; margin-left: 5px; width: 460px; font-size: 17px; line-height: 23px; }
  .welcome .read-more { display: inline-block; margin: 8px 0 0 5px; font-size: 17px; color: var(--white); text-decoration: underline; }
  .welcome .read-more::after { content: ""; display: inline-block; margin-left: 6px; border: 4px solid transparent; border-left-color: var(--muted); }

  .services { position: absolute; left: 560px; top: 646px; width: 530px; }
  .services h2 { font-size: 19px; font-weight: 600; }
  .services .intro { margin-top: 2px; font-size: 12.5px; line-height: 17px; color: var(--soft-white); }
  .services .rule { margin-top: 12px; border-top: 1px dotted rgba(255,255,255,.6); }
  .service { position: absolute; top: 90px; display: flex; gap: 12px; width: 230px; }
  .service.finance { left: 0; }
  .service.consultancy { left: 308px; }
  .service svg { flex: none; }
  .service h3 { font-size: 19px; font-weight: 600; line-height: 24px; }
  .service p { font-size: 12.5px; line-height: 16px; margin-left: 2px; color: var(--soft-white); }
  .service .more { display: block; margin: 6px 0 0 2px; font-size: 13px; font-weight: 600; color: var(--muted); }
  .slider-arrow { position: absolute; top: 744px; }

  .quick-links { position: absolute; left: 110px; top: 874px; display: flex; gap: 30px; }
  .quick-links a { display: flex; justify-content: space-between; align-items: center; width: 223px; height: 37px; padding: 0 10px 0 12px; background: var(--white); border-radius: 3px; font-family: "Raleway", Arial, sans-serif; font-weight: 600; font-size: 18px; color: var(--button-text); text-decoration: none; }

  .footer { position: absolute; left: 0; right: 0; top: 938px; border-top: 1px dotted rgba(255,255,255,.35); }
  .footer p { position: absolute; top: 13px; font-size: 13px; color: var(--muted); }
  .footer .copy { left: 111px; }
  .footer .policy { right: 110px; }
</style>
</head>
<body>
<div class="page">
  <svg class="hero-backdrop" width="1200" height="984" role="img" aria-label="Night skyline of a harbour city with lit towers and waterfront">
    <defs>
      <linearGradient id="sky" x1="0" y1="0" x2="0" y2="1">
        <stop offset="0" stop-color="#0e1c33"/>
        <stop offset=".35" stop-color="#2b4a70"/>
        <stop offset=".5" stop-color="#6c6a78"/>
        <stop offset=".62" stop-color="#3b4258"/>
        <stop offset=".8" stop-color="#5a4630"/>
        <stop offset="1" stop-color="#2a2520"/>
      </linearGradient>
    </defs>
    <rect width="1200" height="984" fill="url(#sky)"/>
  </svg>
  <svg class="hero-shade" width="1200" height="984" aria-hidden="true">
    <polygon points="1140,0 1200,0 1200,984 215,984" fill="var(--shade)"/>
  </svg>

  <header>
    <div class="brand"><span class="brand-mark"></span><span class="brand-name">Valdo Capital</span></div>
    <div class="lang"><span class="current">EN</span> &nbsp;|&nbsp; SP<span class="caret"></span></div>
    <div class="social"><span></span><span></span><span></span></div>
    <nav class="main-nav">
      <a class="active" href="#">HOME</a>
      <a href="#">FINANCIAL PRODUCTS</a>
      <a href="#">TEAM</a>
      <a href="#">NEWS</a>
    </nav>
  </header>

  <section class="welcome">
    <div class="lead">Welcome To</div>
    <h1>Valdo Capital</h1>
    <p>Lorem ipsum dolor sit amet, consectetur adipisicing elit, sed do eiusmod tempor incididunt ut labore et dolore magna aliqua..</p>
    <a class="read-more" href="#">Read More</a>
  </section>

  <svg class="slider-arrow" style="left:524px" width="22" height="44" aria-hidden="true"><polyline points="18,2 4,22 18,42" fill="none" stroke="rgba(255,255,255,.35)" stroke-width="4"/></svg>
  <svg class="slider-arrow" style="left:1106px" width="22" height="44" aria-hidden="true"><polyline points="4,2 18,22 4,42" fill="none" stroke="rgba(255,255,255,.35)" stroke-width="4"/></svg>

  <section class="services">
    <h2>Our Services</h2>
    <p class="intro">Lorem ipsum dolor sit amet, consectetur adipisicing elit, sed do eiusmod tempor incididunt ut labore et dolore magna aliqua..</p>
    <div class="rule"></div>
    <div class="service finance">
      <svg width="48" height="56" aria-hidden="true">
        <rect x="16" y="2" width="22" height="18" rx="2" fill="#fff"/>
        <rect x="4" y="22" width="40" height="24" rx="8" fill="#fff"/>
      </svg>
      <div>
        <h3>Finance</h3>
        <p>Valdo Capital lorem ipsum dolor sit amet..</p>
        <a class="more">Read More ⟶</a>
      </div>
    </div>
    <div class="service consultancy">
      <svg width="52" height="56" aria-hidden="true">
        <circle cx="8" cy="12" r="5" fill="#fff"/>
        <rect x="3" y="19" width="11" height="24" rx="2" fill="#fff"/>
        <rect x="16" y="4" width="34" height="26" fill="none" stroke="#fff" stroke-width="3"/>
        <line x1="33" y1="30" x2="26" y2="44" stroke="#fff" stroke-width="2"/>
        <line x1="33" y1="30" x2="40" y2="44" stroke="#fff" stroke-width="2"/>
      </svg>
      <div>
        <h3>Consultancy</h3>
        <p>Valdo Capital lorem ipsum dolor sit amet..</p>
        <a class="more">Read More ⟶</a>
      </div>
    </div>
  </section>

  <nav class="quick-links">
    <a href="#">About Us <svg width="14" height="24" aria-hidden="true"><polyline points="3,2 11,12 3,22" fill="none" stroke="#1e2228" stroke-width="3"/></svg></a>
    <a href="#">What We Do <svg width="14" height="24" aria-hidden="true"><polyline points="3,2 11,12 3,22" fill="none" stroke="#1e2228" stroke-width="3"/></svg></a>
    <a href="#">Our Blog <svg width="14" height="24" aria-hidden="true"><polyline points="3,2 11,12 3,22" fill="none" stroke="#1e2228" stroke-width="3"/></svg></a>
    <a href="#">Who We Are <svg width="14" height="24" aria-hidden="true"><polyline points="3,2 11,12 3,22" fill="none" stroke="#1e2228" stroke-width="3"/></svg></a>
  </nav>

  <footer class="footer">
    <p class="copy">Copyright © 2014 Valdo Capital. All Rights Reserved</p>
    <p class="policy">Privacy Policy &amp; Term of Uses</p>
  </footer>
</div>
</body>
</html>
```